Brookvale Estates LLC stationary for a real estate property management company.

Create stationary (letterhead, envelopes, business cards) using Brookvale Estates LLC logo as primary creative element. Stationary design needs to be horizontal, leaving as much space as possible for correspondence copy. See attached Creative Brief and past stationary files for details.

Target Market(s)

Prospective apartment residents and current residents, vendors, and government agencies.

Industry/Entity Type

Property Management

Contact Information for Business Card

Business card employee title: Property Manager. Should include address, phone, fax, email, website, slogan, and Brookvale Estates logo.

Font styles to use
Sans Serif

Colors
0592cd
000000

Requirements
Must have
• Tone should be conservative, institutional, business (i.e. banking, finance, real estate). Must include: address, phone, fax, website, and slogan (see attached Creative Brief). Should be a horizontal design, leaving as much room as possible for letter correspondence copy.
Nice to have
• Please use an Arial or Helvetica style font.
Should not have
• Letterhead layout should leave as much room as possible for copy.

```html
<!DOCTYPE html>
<html lang="en">
<head>
<meta charset="utf-8">
<title>Brookvale Estates LLC – Stationery</title>
<link href="https://fonts.googleapis.com/css2?family=Arimo:wght@400;700&family=Source+Sans+3:wght@400&display=swap" rel="stylesheet">
<style>
  :root {
    --brand-blue: #1a67a6;
    --brand-grey: #3f4042;
    --card-dark: #48494b;
    --paper: #f5f5f5;
    --text: #2b2b2b;
    --text-soft: #4a4a4a;
    --backdrop: #e4e0da;
    --flap-line: #bfd3e0;
  }
  * { margin: 0; padding: 0; box-sizing: border-box; }
  html, body { width: 1200px; height: 754px; overflow: hidden; background: var(--backdrop); }
  .canvas { position: relative; width: 1200px; height: 754px; font-family: "Arimo", Arial, sans-serif; }
  .sheet { position: absolute; background: var(--paper); box-shadow: 0 2px 6px rgba(0,0,0,.25); }

  /* Wordmark */
  .wordmark { color: var(--brand-blue); font-weight: 700; line-height: 1; }
  .wordmark__name { display: block; }
  .wordmark__sub { display: block; letter-spacing: .18em; }

  /* Letterhead */
  .letterhead { left: 36px; top: 32px; width: 490px; height: 690px; }
  .letterhead__band { position: absolute; left: 0; top: 38px; width: 30px; height: 44px; background: var(--brand-blue); }
  .letterhead .wordmark { position: absolute; left: 40px; top: 46px; }
  .letterhead .wordmark__name { font-size: 19px; }
  .letterhead .wordmark__sub { font-size: 8px; margin-top: 3px; }
  .letterhead__contact { position: absolute; left: 212px; top: 52px; font-size: 8.2px; line-height: 12px; color: var(--text-soft); }
  .letter { position: absolute; left: 30px; top: 190px; width: 427px; font-family: "Source Sans 3", "Myriad Pro", sans-serif; color: var(--text); }
  .letter__greeting { font-size: 14px; margin-bottom: 22px; }
  .letter p { font-size: 7.6px; line-height: 11.7px; text-align: justify; margin-bottom: 11.7px; }
  .letter__closing { margin-top: 22px; font-size: 7.6px; }
  .letter__signature { display: block; width: 64px; height: 26px; margin-top: 12px; background: linear-gradient(90deg, #dcdde2, #eeeeef); border-radius: 3px; }

  /* Business card front */
  .card { width: 267px; height: 152px; }
  .card--front { left: 577px; top: 74px; overflow: hidden; }
  .card__band { position: absolute; left: 0; top: 0; width: 14px; height: 100%; background: var(--brand-blue); }
  .card__info { position: absolute; right: 11px; top: 20px; text-align: right; color: var(--text-soft); }
  .card--front .wordmark__name { font-size: 20px; }
  .card--front .wordmark__sub { font-size: 8.4px; margin-top: 2px; color: var(--brand-grey); }
  .card__person { margin-top: 10px; font-size: 10px; font-weight: 700; color: var(--brand-blue); }
  .card__title { font-size: 7px; margin-top: 1px; }
  .card__address, .card__contact { font-size: 6.3px; line-height: 8.4px; }
  .card__address { margin-top: 9px; }
  .card__contact { margin-top: 5px; }

  /* Business card back */
  .card--back { left: 877px; top: 143px; background: var(--card-dark); }
  .card__slogan { position: absolute; left: 0; right: 0; top: 129px; text-align: center; color: #fff; font-size: 6.8px; font-weight: 700; }

  /* Envelopes */
  .envelope--back { left: 615px; top: 350px; width: 548px; height: 248px; }
  .envelope__flap { position: absolute; left: 0; top: 0; }
  .envelope--front { left: 547px; top: 470px; width: 550px; height: 250px; }
  .envelope--front .wordmark { position: absolute; left: 23px; top: 38px; }
  .envelope--front .wordmark__name { font-size: 18px; }
  .envelope--front .wordmark__sub { font-size: 7.4px; margin-top: 2px; color: var(--brand-grey); }
  .envelope__return { position: absolute; left: 38px; top: 72px; font-size: 7.6px; line-height: 10px; color: var(--text-soft); }
</style>
</head>
<body>
<main class="canvas">

  <section class="sheet letterhead">
    <div class="letterhead__band"></div>
    <div class="wordmark">
      <span class="wordmark__name">BROOKVALE</span>
      <span class="wordmark__sub">ESTATES LLC</span>
    </div>
    <div class="letterhead__contact">
      2750 Alder Ridge Road #B210, Fairhaven, CA 90415<br>
      P: 555-210-4470 | F: 555-210-4471 | www.brookvaleestates.us
    </div>
    <article class="letter">
      <p class="letter__greeting">Dear Mr. Carter,</p>
      <p>Lorem ipsum dolor sit amet, consectetur adipiscing elit. Donec orci purus, luctus vitae dignissim eu, iaculis sed purus. Vivamus faucibus, ipsum nec aliquet viverra, leo mauris condimentum ligula, sit amet sagittis enim ligula quis arcu. Nam egestas tortor id nisi porttitor mattis. In tortor ante, ultricies in suscipit a, tempus non massa. Vivamus et auctor mi. Fusce vel massa nulla. Phasellus nec eros mauris, et scelerisque orci.</p>
      <p>Donec malesuada orci vitae nulla accumsan porta a id massa. Quisque accumsan iaculis magna sit amet fringilla. Maecenas consequat, magna eget tincidunt semper, odio nibh rutrum mi, id feugiat ante nisi eu risus. Vestibulum nunc orci, rhoncus a placerat in, ultricies in mi. Cras mattis varius eros, vel fringilla nisi suscipit eget. Quisque scelerisque sagittis nulla at porttitor.</p>
      <p>Sed id augue vitae urna euismod commodo aliquet a quam. Pellentesque arcu velit, cursus et malesuada ut, consequat et diam. Nullam erat sem, rhoncus id ullamcorper vitae, rhoncus et arcu. In ultricies ultricies nulla, ut rutrum nisi iaculis at. Donec eu magna a metus ornare faucibus. Fusce aliquet faucibus ultricies. Morbi semper, est id tincidunt gravida, sem arcu adipiscing lacus, ac bibendum nulla leo eu purus. Quisque nec diam sed risus consectetur a accumsan quis quis nibh. Vestibulum id purus lorem.</p>
      <p>It is a long established fact that a reader will be distracted by the readable content of a page when looking at its layout. The point of using Lorem Ipsum is that it has a more-or-less normal distribution of letters, as opposed to using 'Content here, content here', making it look like readable English. Many desktop publishing packages</p>
      <p class="letter__closing">Sincerely,</p>
      <span class="letter__signature" role="img" aria-label="Handwritten signature"></span>
    </article>
  </section>

  <section class="sheet card card--front">
    <div class="card__band"></div>
    <div class="card__info">
      <div class="wordmark">
        <span class="wordmark__name">BROOKVALE</span>
        <span class="wordmark__sub">ESTATES LLC</span>
      </div>
      <div class="card__person">DANIEL HARTLEY</div>
      <div class="card__title">Property Manager</div>
      <div class="card__address">2750 Alder Ridge Road #B210<br>Fairhaven, CA 90415</div>
      <div class="card__contact">Phone: 555-210-4470<br>Fax: 555-210-4471<br>daniel@brookvaleestates.us<br>www.brookvaleestates.us</div>
    </div>
  </section>

  <section class="sheet card card--back">
    <p class="card__slogan">Multifamily Property Management</p>
  </section>

  <section class="sheet envelope--back">
    <svg class="envelope__flap" width="548" height="100" viewBox="0 0 548 100">
      <path d="M12 0 L22 78 Q25 91 40 91 L508 91 Q523 91 526 78 L536 0" fill="none" stroke="var(--flap-line)" stroke-width="1"/>
    </svg>
  </section>

  <section class="sheet envelope--front">
    <div class="wordmark">
      <span class="wordmark__name">BROOKVALE</span>
      <span class="wordmark__sub">ESTATES LLC</span>
    </div>
    <div class="envelope__return">2750 Alder Ridge Road #B210<br>Fairhaven, CA 90415</div>
  </section>

</main>
</body>
</html>
```